Velmoria-Quillmesh Partial Redesign - Web App

Are you able to apply your creativity to an existing layout? I’m convinced that even just a few touches can make a big difference to add personality and professionalism to a website design, and I’m looking for someone able to use existing ideas and bring them to the next level while keeping inside some given constraints.
The actual job is to improve an existing design concept and to apply it creatively to a landing page, a simple home page, and an older web app (single page website).
To help you start with a clear picture of the current situation and of my requirements, I created a detailed brief with screenshots, live examples, and complete instructions. You can find it attached to this job.
My tastes are inclined towards clean and simple designs. For this project I'm not looking for dazzling novelty, but for very solid craftsmanship. Are the right man - or woman - for the job?
Updates
I wanted to thank everybody who participated in this project. I made a choice, but also other designs were interesting. Hope to work with you another time.
Target Market(s)
Our main target is social media marketers and startuppers
Look and feel
Each slider illustrates characteristics of the customer's brand and the style your logo design should communicate.

```html
<!DOCTYPE html>
<html lang="en">
<head>
<meta charset="utf-8">
<title>Velmoria – Hashtag Explorer</title>
<link href="https://fonts.googleapis.com/css2?family=Arimo:wght@400;700&family=Open+Sans:wght@400;600&display=swap" rel="stylesheet">
<style>
:root{
  --black:#000;
  --ink:#333;
  --text:#444;
  --muted:#888;
  --blue:#0a6ea0;
  --blue-dark:#0e5f8a;
  --cyan:#1ab0e0;
  --red:#e00d00;
  --node:#c4c4c4;
  --hub:#3a3c40;
  --line:#e2e2e2;
}
*{margin:0;padding:0;box-sizing:border-box}
html,body{width:1200px;height:765px;overflow:hidden;background:#fff;font-family:"Arimo",Arial,sans-serif;color:var(--text)}
.page{position:relative;width:1200px;height:765px;overflow:hidden}
.topbar{position:absolute;left:0;top:0;width:1200px;height:39px;background:var(--black)}
.nav{position:absolute;left:195px;top:13px;display:flex;font-size:11px;color:#ddd;letter-spacing:.2px}
.nav span{margin-right:37px}
.login{position:absolute;top:7px;height:23px;padding:0 13px;line-height:21px;font-size:10px;color:#eee;background:linear-gradient(#6a6a6a,#3a3a3a);border:1px solid #777;border-radius:3px}
.login.admin{left:843px}.login.user{left:940px}
.header{position:absolute;left:0;top:39px;width:1200px;height:64px;border-bottom:1px solid var(--line);box-shadow:0 2px 3px rgba(0,0,0,.06)}
.brand{position:absolute;left:258px;top:13px}
.brand-name{font-weight:700;font-size:25px;color:var(--ink);letter-spacing:-.5px;line-height:1}
.brand-tag{font-size:8px;color:var(--ink);margin-left:8px;margin-top:1px}
.search-box{position:absolute;left:533px;top:20px;width:210px;height:21px;border:1px solid #d0d0d0;border-radius:4px;background:linear-gradient(#e4e4e4,#f4f4f4)}
.search-btn{position:absolute;left:748px;top:21px;width:64px;height:19px;background:linear-gradient(#1c8cc4,#0a6ea0);color:#fff;font-size:10px;text-align:center;line-height:19px;border-radius:2px}
.divider{position:absolute;left:831px;top:4px;width:1px;height:56px;background:var(--line)}
.counter{position:absolute;left:855px;top:13px;font-size:8.5px;line-height:10px;color:var(--blue)}
.digits{display:flex;gap:2px;margin-top:5px}
.digits span{display:block;width:14px;height:14px;border:1px solid #bcd;border-radius:2px;text-align:center;line-height:12px;font-size:10px;color:var(--blue);background:#fff}
.digits span.sep{width:12px}
.counter small{display:block;margin-top:5px;color:var(--muted);font-size:9px;line-height:10px}
.graph{position:absolute;left:171px;top:154px;width:463px;height:394px}
.graph text{font-family:"Open Sans",Arial,sans-serif;fill:#fff;text-anchor:middle;dominant-baseline:middle}
.mode{position:absolute;top:579px;height:33px;border-radius:3px;font-weight:700;font-size:16px;text-align:center;line-height:31px;color:#0b5a85;text-shadow:0 1px 0 rgba(255,255,255,.4);border:1px solid #0a6ea0;box-shadow:0 2px 3px rgba(0,0,0,.25)}
.mode.simple{left:258px;width:158px;background:linear-gradient(#35b6e6,#0d86bf)}
.mode.advanced{left:430px;width:176px;background:linear-gradient(#4fd0f5,#15a9e0)}
.follow{position:absolute;left:706px;top:117px;width:323px;height:63px;background:linear-gradient(#1a9fd2,#0b78ad);border:1px solid #0a6ea0;text-align:center;line-height:61px;color:#3ecaf5;font-weight:700;font-size:19px;letter-spacing:1px;white-space:nowrap}
.tweets{position:absolute;left:706px;top:180px;width:323px}
.tweet{position:relative;height:63.5px;background:linear-gradient(#fbfbfb,#ececec);border:1px solid #dadada;border-top:none}
.avatar{position:absolute;left:8px;top:7px;width:62px;height:50px;border:2px solid #fff;box-shadow:0 0 0 1px #ccc}
.tweet p{position:absolute;left:78px;top:13px;width:240px;font-size:9.5px;line-height:14px;color:#444}
.ago{position:absolute;right:8px;top:44px;width:78px;height:15px;background:#fff;border:1px solid #ccc;font-size:7.5px;color:var(--muted);line-height:13px;padding-left:8px}
.ago i{position:absolute;right:5px;top:3px;width:9px;height:7px;border-radius:50%;background:#3a9fd6}
.influencers h2{position:absolute;left:707px;top:452px;font-size:16px;color:var(--blue-dark);font-weight:700}
.influ-list{position:absolute;left:706px;top:481px;width:323px;list-style:none}
.influ-list li{position:relative;height:29px;line-height:29px;padding-left:12px;font-size:10.5px;color:#333;border-bottom:1px solid var(--line)}
.influ-list li.top{color:var(--blue-dark)}
.followers{position:absolute;right:0;top:4px;height:20px;line-height:18px;padding:0 7px;border:1px solid #ccc;border-radius:3px;color:var(--blue-dark);background:#fff;font-size:10.5px}
.footer{position:absolute;left:0;top:670px;width:1200px;height:95px;background:linear-gradient(#16a0d2,#0a76ad)}
.foot-brand{position:absolute;left:258px;top:30px}
.foot-brand .brand-name{color:#000}
.foot-brand .brand-tag{color:#111}
.copy{position:absolute;left:290px;top:17px;font-size:9.5px;color:#fff}
.follow-us{position:absolute;left:663px;top:22px;font-size:13px;font-weight:700;color:#fff;letter-spacing:.5px}
.network{position:absolute;top:40px;font-size:17px;font-weight:700;color:#7fd8f8;white-space:nowrap}
.network.friendsy{left:662px}
.network.chirpline{left:760px}
.network.workwire{left:860px}
.network.searcha{left:950px}
.c8{position:absolute;left:1058px;top:44px;font-size:11px;color:#fff}
</style>
</head>
<body>
<div class="page">
  <div class="topbar">
    <div class="nav"><span>HOME</span><span>ABOUT</span><span>BLOG</span><span>SUMMARY</span><span>TIMELINE</span><span>INFLUENCERS</span><span>HASHTAGS</span></div>
    <div class="login admin">ADMIN LOGIN</div>
    <div class="login user">USER LOGIN</div>
  </div>

  <header class="header">
    <div class="brand">
      <div class="brand-name">Velmoria</div>
      <div class="brand-tag">CyberSocial Branding Intelligence</div>
    </div>
    <div class="search-box"></div>
    <div class="search-btn">SEARCH</div>
    <div class="divider"></div>
    <div class="counter">HASHTAGS FOUND SO FAR:
      <div class="digits"><span>1</span><span>0</span><span class="sep">,</span><span>6</span><span>1</span><span>1</span><span class="sep">,</span><span>1</span><span>8</span><span>0</span></div>
      <small>in 567,419,411 tweets</small>
    </div>
  </header>

  <svg class="graph" viewBox="200 180 540 460" aria-label="Hashtag network">
    <defs><polygon id="penta" points="0,-1 0.951,-0.309 0.588,0.809 -0.588,0.809 -0.951,-0.309"/></defs>
    <g stroke="#555" stroke-width="2.5">
      <line x1="518" y1="430" x2="316" y2="245"/><line x1="518" y1="430" x2="490" y2="262"/>
      <line x1="518" y1="430" x2="632" y2="342"/><line x1="518" y1="430" x2="350" y2="378"/>
      <line x1="518" y1="430" x2="260" y2="467"/><line x1="518" y1="430" x2="412" y2="506"/>
      <line x1="518" y1="430" x2="519" y2="575"/><line x1="518" y1="430" x2="650" y2="500"/>
    </g>
    <g fill="#c4c4c4">
      <use href="#penta" transform="translate(316 245) rotate(10) scale(38)"/>
      <use href="#penta" transform="translate(632 342) rotate(15) scale(54)"/>
      <use href="#penta" transform="translate(350 378) rotate(-10) scale(62)"/>
      <use href="#penta" transform="translate(260 467) rotate(10) scale(37)"/>
      <use href="#penta" transform="translate(412 506) rotate(-5) scale(47)"/>
      <use href="#penta" transform="translate(519 575) rotate(0) scale(56)"/>
      <use href="#penta" transform="translate(650 500) rotate(15) scale(74)"/>
    </g>
    <use href="#penta" fill="#e00d00" transform="translate(490 262) scale(74)"/>
    <use href="#penta" fill="#3a3c40" transform="translate(518 430) rotate(20) scale(64)"/>
    <g font-size="19">
      <text x="316" y="247">a</text><text x="490" y="264">you</text><text x="632" y="342">to</text>
      <text x="350" y="378">everything</text><text x="516" y="431">Hastag</text><text x="260" y="468">every</text>
      <text x="412" y="510">when</text><text x="519" y="573">que</text><text x="650" y="506">People</text>
    </g>
  </svg>

  <div class="mode simple">Simple Mode</div>
  <div class="mode advanced">Advanced Mode</div>

  <div class="follow">FOLLOW ME ON Chirpline</div>
  <div class="tweets">
    <div class="tweet"><div class="avatar" role="img" aria-label="User profile photo" style="background:linear-gradient(135deg,#6aa3c8,#3b3b3b)"></div><p>MaraVell1: JUNE IS SO COOL AND SO FUNNY #bestie #shethinksshe'scool #hashtags #lolzers #fun</p><div class="ago">8 hours ago<i></i></div></div>
    <div class="tweet"><div class="avatar" role="img" aria-label="User profile photo" style="background:linear-gradient(135deg,#e8e0c8,#b58a6a)"></div><p>MaraVell1: JUNE IS SO COOL AND SO FUNNY #bestie #shethinksshe'scool #hashtags #lolzers #fun</p><div class="ago">8 hours ago<i></i></div></div>
    <div class="tweet"><div class="avatar" role="img" aria-label="User profile photo" style="background:linear-gradient(135deg,#f0ece6,#9a5a34)"></div><p>MaraVell1: JUNE IS SO COOL AND SO FUNNY #bestie #shethinksshe'scool #hashtags #lolzers #fun</p><div class="ago">8 hours ago<i></i></div></div>
    <div class="tweet"><div class="avatar" role="img" aria-label="User profile photo" style="background:linear-gradient(135deg,#7fa6c6,#d2a27c)"></div><p>MaraVell1: JUNE IS SO COOL AND SO FUNNY #bestie #shethinksshe'scool #hashtags #lolzers #fun</p><div class="ago">8 hours ago<i></i></div></div>
  </div>

  <section class="influencers">
    <h2>The top 6 influencers for #tag</h2>
    <ul class="influ-list">
      <li class="top">Support<span class="followers">1,769,782 followers</span></li>
      <li>Tobinmarsh</li><li>RKHollow</li><li>Stillwavering</li><li>Daleporter</li><li>Rio_Sendero</li>
    </ul>
  </section>

  <footer class="footer">
    <div class="copy">Copyright (c) 2011-2012</div>
    <div class="foot-brand">
      <div class="brand-name">Velmoria</div>
      <div class="brand-tag">CyberSocial Branding Intelligence</div>
    </div>
    <div class="follow-us">Follow Us :</div>
    <span class="network friendsy">Friendsy</span>
    <span class="network chirpline">Chirpline</span>
    <span class="network workwire">Workwire</span>
    <span class="network searcha">Searcha+</span>
    <div class="c8">C8</div>
  </footer>
</div>
</body>
</html>
```